Brightmill Data Works

Our company is about IT hardwares and IT solutions. IT hardware such as PC, RAMS, storage and servers. IT solutions such as project management, BA. We are also selling new technology too.

Target Market(s)

Consumer, Small to Medium Business, Corporate

Requirements
Must have
• The business card must have the following:
• Name:
• Title:
• Contact Number:
• Email address:
• Website:
• Color: Must match the logo color upgrade

```html
<!DOCTYPE html>
<html lang="en">
<head>
<meta charset="utf-8">
<title>Brightmill Data Works – Business Card</title>
<link rel="stylesheet" href="https://fonts.googleapis.com/css2?family=Lato:wght@400;700;900&family=Russo+One&display=swap">
<style>
  :root {
    --canvas: #1c1c1c;
    --card: #161616;
    --gold: #e59a2a;
    --white: #f4f4f4;
    --grey-mark: #5b5b5b;
    --text-soft: #e6e6e6;
  }
  * { margin: 0; padding: 0; box-sizing: border-box; }
  html, body {
    width: 1200px; height: 900px; overflow: hidden;
    background: var(--canvas);
  }
  .canvas {
    width: 1200px; height: 900px;
    display: flex; flex-direction: column;
    align-items: center; justify-content: center; gap: 70px;
  }
  .card {
    position: relative;
    width: 600px; height: 343px;
    background: var(--card);
    border-radius: 14px;
    overflow: hidden;
    box-shadow: 0 18px 40px rgba(0,0,0,.45);
  }
  .card__edge {
    position: absolute; left: 0; right: 0; bottom: 0;
    height: 7px; background: var(--gold);
  }

  .brand {
    display: flex; align-items: center;
  }
  .brand__square { flex: none; background: var(--gold); }
  .brand__name {
    font-family: "Russo One", sans-serif;
    text-transform: uppercase;
    line-height: 1.1;
    white-space: nowrap;
  }
  .brand__line { display: block; }

  /* Front */
  .card--front {
    display: flex; align-items: center; justify-content: center;
    padding: 0 70px 10px;
  }
  .card--front .brand { gap: 18px; }
  .card--front .brand__square { width: 24px; height: 24px; }
  .card--front .brand__name {
    font-size: 40px; letter-spacing: 1px; color: var(--white);
  }

  /* Back */
  .card--back { display: flex; }
  .back__brand {
    width: 52%;
    display: flex; align-items: center; justify-content: center;
    padding: 70px 24px 0 40px;
  }
  .back__brand .brand { gap: 12px; }
  .back__brand .brand__square { width: 16px; height: 16px; }
  .back__brand .brand__name {
    font-size: 24px; letter-spacing: .5px; color: var(--grey-mark);
  }
  .back__divider {
    width: 2px; flex: none; background: var(--gold);
    margin: 86px 0 100px;
  }
  .contact {
    flex: 1;
    padding: 80px 20px 0 34px;
    font-family: "Lato", sans-serif;
  }
  .contact__name {
    font-size: 19px; color: var(--gold); text-transform: uppercase;
    font-weight: 400; white-space: nowrap;
  }
  .contact__name strong { font-weight: 900; }
  .contact__title {
    font-size: 13px; color: var(--text-soft); margin: 3px 0 22px 14px;
  }
  .contact__line {
    display: flex; align-items: center; gap: 10px;
    font-size: 14px; color: var(--text-soft);
    margin: 0 0 9px 30px; white-space: nowrap;
  }
  .contact__line svg { width: 15px; height: 15px; flex: none; }
  .contact__web {
    font-size: 15px; font-weight: 900; color: var(--gold);
    margin: 10px 0 0 44px; white-space: nowrap;
  }
</style>
</head>
<body>
<main class="canvas">

  <section class="card card--front" aria-label="Card front">
    <div class="brand">
      <span class="brand__square"></span>
      <span class="brand__name">
        <span class="brand__line">Brightmill</span>
        <span class="brand__line">Data Works</span>
      </span>
    </div>
    <div class="card__edge"></div>
  </section>

  <section class="card card--back" aria-label="Card back">
    <div class="back__brand">
      <div class="brand">
        <span class="brand__square"></span>
        <span class="brand__name">
          <span class="brand__line">Brightmill</span>
          <span class="brand__line">Data Works</span>
        </span>
      </div>
    </div>
    <div class="back__divider"></div>
    <div class="contact">
      <p class="contact__name">Nora <strong>Whitcombe</strong></p>
      <p class="contact__title">Managing Director</p>
      <p class="contact__line">
        <svg viewBox="0 0 16 16" aria-hidden="true"><path fill="var(--gold)" d="M3 2h3l1.5 3.5-2 1.3a8 8 0 0 0 3.7 3.7l1.3-2L14 10v3a1 1 0 0 1-1 1A11 11 0 0 1 2 3a1 1 0 0 1 1-1z"/></svg>
        01632 960418
      </p>
      <p class="contact__line">
        <svg viewBox="0 0 16 16" aria-hidden="true"><rect x="1.5" y="3.5" width="13" height="9" fill="none" stroke="var(--gold)" stroke-width="1.6"/><path d="M1.5 3.5 8 9l6.5-5.5" fill="none" stroke="var(--gold)" stroke-width="1.6"/></svg>
        admin@brightmilldata.co.uk
      </p>
      <p class="contact__web">www.brightmilldata.co.uk</p>
    </div>
    <div class="card__edge"></div>
  </section>

</main>
</body>
</html>
```